A5 Flyer for Financial Services Business

I am after a re-design of our business flyer to fit in with our new branding style and logo colour scheme. Wanting something with a bit of designer flair that I could not create myself. I have included the flyer which I created which lacks style so dazzle me.

I want to use the same content.

Text for main body of flyer is

Are you a small business owner, tradie or TRPQ Service Provider struggling to stay on top of your bookkeeping and compliance obligations? If so we would love to help you get back on track and take control of your business finances so that you can make informed business decisions and focus on what you do best.

We have over 20 years industry experience and, as a small business ourselves, we are able to offer our clients a personal bookkeeping solution tailored to meet the needs of your business.

Accounts Payable | Accounts Receivable
Customer Invoicing
Bank and Credit Card Reconciliations
Payroll | Superannuation | Payroll Tax
Business Activity | Instalment Activity Statements
Regular Financial Reports
Vantly and Brimfolk Set-Up and Training

```html
<!DOCTYPE html>
<html lang="en">
<head>
<meta charset="utf-8">
<title>Even Ledger Financial Services – Flyer</title>
<link rel="stylesheet" href="https://fonts.googleapis.com/css2?family=Oswald:wght@500;600&family=Roboto:wght@300;400;500;700&display=swap">
<style>
  :root{
    --stage:#232323;
    --paper:#f6f7f8;
    --ink:#2f3236;
    --body:#4a4d52;
    --teal:#0f8088;
    --teal-bright:#19a99f;
    --teal-deep:#06536a;
    --charcoal:#333538;
    --white:#ffffff;
  }
  *{margin:0;padding:0;box-sizing:border-box}
  html,body{width:1200px;height:1200px;overflow:hidden;background:var(--stage)}
  .flyer{position:absolute;left:207px;top:45px;width:786px;height:1110px;background:var(--paper);overflow:hidden;font-family:'Roboto',sans-serif;box-shadow:0 10px 30px rgba(0,0,0,.5)}
  .shapes{position:absolute;left:0;top:0}
  .brand{position:absolute;left:34px;top:64px;width:262px;text-align:center}
  .brand-mark{display:block;width:44px;height:44px;margin:0 auto 10px;background:var(--teal)}
  .brand-name{font-family:'Roboto',sans-serif;font-weight:400;font-size:29px;letter-spacing:-1px;color:var(--teal);line-height:1;white-space:nowrap}
  .brand-sub{font-family:'Roboto',sans-serif;font-weight:400;font-size:14px;letter-spacing:8.4px;color:var(--teal);margin-top:6px;white-space:nowrap}
  .headline{position:absolute;left:34px;top:456px;font-family:'Oswald',sans-serif;font-weight:600;font-size:35px;line-height:44.5px;color:var(--teal);white-space:nowrap}
  .badge{position:absolute;left:598px;top:571px;width:64px;height:64px;border-radius:50%;background:#e9ecee;border:3px solid #3b3d40}
  .badge::after{content:"";position:absolute;left:12px;top:12px;width:34px;height:34px;border-radius:50%;background:#a7c53a}
  .agent{position:absolute;left:668px;top:589px;width:90px;height:36px;background:var(--charcoal);color:var(--white);font-size:13.5px;line-height:17px;text-align:center;padding-top:1px}
  .lead{position:absolute;left:34px;top:645px;width:730px;font-size:24.5px;font-weight:500;line-height:32px;color:var(--ink)}
  .lead em{font-style:normal;color:var(--teal)}
  .copy{position:absolute;left:34px;width:286px;font-size:15.8px;font-weight:300;line-height:25.3px;color:var(--body);text-align:justify}
  .copy-intro{top:727px}
  .copy-story{top:901px}
  .rule{position:absolute;left:35px;top:880px;width:156px;height:5px;background:var(--teal)}
  .services{position:absolute;left:351px;top:726px;list-style:none}
  .services::before{content:"";position:absolute;left:16px;top:20px;width:2px;height:228px;background:var(--teal-deep)}
  .service{position:relative;height:38px;padding-left:38px;font-size:16.6px;font-weight:500;color:var(--ink);line-height:32px;white-space:nowrap}
  .service-icon{position:absolute;left:2px;top:2px;width:30px;height:30px;border-radius:50%;background:var(--white);border:2.5px solid var(--teal-deep)}
  .service-icon::after{content:"";position:absolute;left:8px;top:6px;width:10px;height:13px;border:1.5px solid var(--teal-deep);border-radius:2px}
  .partners{position:absolute;left:345px;top:1000px;width:441px;height:44px;background:var(--charcoal);clip-path:polygon(26px 0,100% 0,100% 100%,0 100%);display:flex;align-items:center;padding-left:32px;color:var(--white);font-size:14px;font-weight:500;white-space:nowrap}
  .partner{display:flex;align-items:center;gap:7px}
  .partner-dot{width:26px;height:26px;border-radius:50%;background:var(--teal-bright);flex:none}
  .partner-square{width:12px;height:12px;background:#2ca01c;flex:none}
  .partner-divider{width:3px;height:22px;background:var(--white);margin:0 12px;flex:none}
  .footer{position:absolute;left:0;top:1046px;width:786px;height:64px;background:linear-gradient(90deg,var(--teal-bright),#0c7f89 55%,var(--teal-deep));border-top:2px solid var(--white)}
  .footer-item{position:absolute;top:0;height:62px;display:flex;align-items:center;gap:9px;color:var(--white);white-space:nowrap}
  .web{left:34px;font-size:19.5px;font-weight:500}
  .phone{left:562px;font-size:26px;font-weight:700;letter-spacing:.3px}
  .footer svg{display:block}
</style>
</head>
<body>
<div class="flyer">
  <svg class="shapes" width="786" height="640" viewBox="0 0 786 640">
    <defs>
      <linearGradient id="photoTone" x1="0" y1="0" x2="1" y2="0.3">
        <stop offset="0" stop-color="#eef3f2"/>
        <stop offset="0.45" stop-color="#a9d7d1"/>
        <stop offset="0.8" stop-color="#2c9e98"/>
        <stop offset="1" stop-color="#1a7f86"/>
      </linearGradient>
      <linearGradient id="tealLeft" x1="0" y1="0" x2="1" y2="1">
        <stop offset="0" stop-color="#1aa9a0"/>
        <stop offset="0.6" stop-color="#0a7085"/>
        <stop offset="1" stop-color="#064c66"/>
      </linearGradient>
      <linearGradient id="tealRight" x1="0" y1="1" x2="1" y2="0">
        <stop offset="0" stop-color="#0d8f92"/>
        <stop offset="1" stop-color="#19ae9f"/>
      </linearGradient>
    </defs>
    <rect width="786" height="620" fill="url(#photoTone)" role="img" aria-label="Photo of a smiling businesswoman in a navy suit pointing towards the logo, in front of a laptop showing a bar chart"/>
    <polygon points="0,337 380,601 786,505 786,640 0,640" fill="var(--paper)"/>
    <polygon points="0,326 470,420 560,470 526,499 0,338" fill="#333538"/>
    <polygon points="0,338 526,499 380,601" fill="url(#tealLeft)"/>
    <polygon points="786,315 786,505 380,601 526,499" fill="url(#tealRight)"/>
  </svg>

  <div class="brand">
    <span class="brand-mark"></span>
    <div class="brand-name">EVEN LEDGER</div>
    <div class="brand-sub">Financial Services</div>
  </div>

  <h1 class="headline">Are you a<br>small business<br>owner, tradie or<br>TRPQ Service Provider</h1>

  <div class="badge"></div>
  <div class="agent">BAS agent<br>10473829</div>

  <p class="lead">struggling to stay on top of your <em>bookkeeping</em> and <em>compliance</em> obligations?</p>

  <p class="copy copy-intro">If so we would love to help you get back on track and take control of your business finances so that you can make informed business decisions and focus on what you do best.</p>
  <div class="rule"></div>
  <p class="copy copy-story">We have over 20 years industry experience and, as a small business ourselves, we are able to offer our clients a personal bookkeeping solution tailored to meet the needs of your business.</p>

  <ul class="services">
    <li class="service"><span class="service-icon"></span>Accounts Payable | Accounts Receivable</li>
    <li class="service"><span class="service-icon"></span>Customer Invoicing</li>
    <li class="service"><span class="service-icon"></span>Bank and Credit Card Reconciliations</li>
    <li class="service"><span class="service-icon"></span>Payroll | Superannuation | Payroll Tax</li>
    <li class="service"><span class="service-icon"></span>Business Activity | Instalment Activity Statements</li>
    <li class="service"><span class="service-icon"></span>Regular Financial Reports</li>
    <li class="service"><span class="service-icon"></span>Vantly and Brimfolk Set-Up and Training</li>
  </ul>

  <div class="partners">
    <div class="partner"><span class="partner-dot"></span><span>Vantly Certified Advisor</span></div>
    <span class="partner-divider"></span>
    <div class="partner"><span class="partner-square"></span><span>Brimfolk Pro Advisor</span></div>
  </div>

  <footer class="footer">
    <div class="footer-item web">
      <svg width="26" height="26" viewBox="0 0 26 26" fill="none" stroke="#fff" stroke-width="1.4"><circle cx="13" cy="13" r="12"/><circle cx="13" cy="13" r="7"/><ellipse cx="13" cy="13" rx="3" ry="7"/><line x1="6" y1="13" x2="20" y2="13"/></svg>
      www.evenledgerfinancial.com.au
    </div>
    <div class="footer-item phone">
      <svg width="26" height="26" viewBox="0 0 26 26" fill="none" stroke="#fff" stroke-width="1.4"><circle cx="13" cy="13" r="12"/><path d="M9 7c-1 1-1.5 2 -.5 4.5s3.5 5.5 6 6.5 3 .5 4-.5l-2.5-2.5-1.5 1c-1.5-.8-3-2.3-3.8-3.8l1-1.5z" fill="#fff"/></svg>
      0400 182 736
    </div>
  </footer>
</div>
</body>
</html>
```